Whitcombe Business Card Design

The name of the business is Dario Whitcombe, CPA LLC
The service that we offer is Accounting, Tax & Consulting Services. I need it to have the following items:
Dario Whitcombe, Principal
Phone Number
Email Address
Physical Address

I have attached the company logo, one in black and one in white. Please provide a design in black background and the other in white background. Please include "Accounting, Tax & Consulting Services". I want the business card to be clean and very professional.

```html
<!DOCTYPE html>
<html lang="en">
<head>
<meta charset="utf-8">
<title>Dario Whitcombe, CPA LLC — Business Cards</title>
<link rel="stylesheet" href="https://fonts.googleapis.com/css2?family=Montserrat:wght@400;500&family=Mulish:wght@300;400&display=swap">
<style>
  :root {
    --stage: #1e1e1f;
    --card-light: #e6e7e8;
    --card-dark: #3a3a3c;
    --ink: #3d3d3f;
    --ink-soft: #6d6e71;
    --accent: #a3262b;
    --white: #ffffff;
  }
  * { margin: 0; padding: 0; box-sizing: border-box; }
  html, body { width: 1200px; height: 1200px; overflow: hidden; background: var(--stage); }
  .sheet { position: relative; width: 1200px; height: 1200px; }

  .card {
    position: absolute;
    width: 744px;
    height: 429px;
    box-shadow: 0 6px 18px rgba(0,0,0,.45);
  }
  .card--front { left: 252px; top: 172px; background: var(--card-light); }
  .card--back  { left: 250px; top: 646px; background: var(--card-dark); }

  .brand {
    position: absolute;
    font-family: "Montserrat", sans-serif;
    font-weight: 500;
    letter-spacing: 0.5px;
    white-space: nowrap;
  }
  .brand__name { display: block; }
  .brand__tagline {
    display: block;
    font-family: "Mulish", sans-serif;
    font-weight: 400;
    letter-spacing: 2.2px;
    text-transform: uppercase;
  }

  .card--front .brand { left: 54px; top: 56px; }
  .card--front .brand__name { font-size: 20px; color: var(--ink); text-transform: uppercase; }
  .card--front .brand__tagline { font-size: 13px; color: var(--ink-soft); margin-top: 1px; }

  .person { position: absolute; left: 447px; top: 54px; font-family: "Montserrat", sans-serif; }
  .person__name { font-size: 24px; font-weight: 400; color: var(--ink); text-transform: uppercase; letter-spacing: 0.5px; }
  .person__first { color: var(--accent); }
  .person__role { font-family: "Mulish", sans-serif; font-size: 16px; color: var(--ink); margin-top: 2px; }

  .contact { position: absolute; left: 452px; top: 256px; font-family: "Mulish", sans-serif; list-style: none; }
  .contact__address { font-size: 15.5px; line-height: 25px; color: var(--accent); margin-bottom: 4px; }
  .contact__item { display: flex; align-items: center; font-size: 15.5px; line-height: 25px; color: var(--ink); }
  .contact__icon { width: 12px; height: 12px; margin-right: 12px; fill: var(--accent); flex: none; }

  .mark { position: absolute; display: flex; align-items: center; white-space: nowrap; font-family: "Montserrat", sans-serif; font-weight: 500; }
  .mark__square { display: block; flex: none; }
  .card--front .mark { left: 58px; top: 300px; font-size: 13px; color: var(--ink); }
  .card--front .mark__square { width: 60px; height: 60px; background: var(--ink); margin-right: 14px; }

  .card--back .lockup { position: absolute; left: 115px; top: 178px; display: flex; align-items: center; }
  .card--back .mark__square { width: 66px; height: 66px; background: var(--white); margin-right: 22px; }
  .card--back .brand { position: static; color: var(--white); }
  .card--back .brand__name { font-size: 30px; text-transform: uppercase; letter-spacing: 0.3px; }
  .card--back .brand__tagline { font-size: 20px; margin-top: 2px; }

  .services {
    position: absolute; left: 0; right: 0; top: 374px;
    text-align: center;
    font-family: "Mulish", sans-serif; font-weight: 300;
    font-size: 27px; color: var(--white);
  }
</style>
</head>
<body>
<main class="sheet">
  <section class="card card--front" aria-label="Business card, white side">
    <div class="brand">
      <span class="brand__name">Dario Whitcombe, CPA LLC</span>
      <span class="brand__tagline">Certified Public Accountant</span>
    </div>

    <div class="person">
      <p class="person__name"><span class="person__first">Dario</span> Whitcombe</p>
      <p class="person__role">Principal</p>
    </div>

    <div class="mark">
      <span class="mark__square"></span>
    </div>

    <ul class="contact">
      <li class="contact__address">PO Box 2870 Larchmont<br>Edmonton, AB T5K 3R8</li>
      <li class="contact__item">
        <svg class="contact__icon" viewBox="0 0 24 24" aria-hidden="true"><path d="M6.6 10.8a15 15 0 0 0 6.6 6.6l2.2-2.2a1 1 0 0 1 1-.25 11.4 11.4 0 0 0 3.6.57 1 1 0 0 1 1 1V20a1 1 0 0 1-1 1A17 17 0 0 1 3 4a1 1 0 0 1 1-1h3.5a1 1 0 0 1 1 1c0 1.25.2 2.45.57 3.57a1 1 0 0 1-.25 1z"/></svg>
        780 (0) 555 204 817
      </li>
      <li class="contact__item">
        <svg class="contact__icon" viewBox="0 0 24 24" aria-hidden="true"><path d="M2 5h20v14H2z M2 5l10 8 10-8" /></svg>
        dario@whitcombecpa.ca
      </li>
      <li class="contact__item">
        <svg class="contact__icon" viewBox="0 0 24 24" aria-hidden="true"><circle cx="12" cy="12" r="10"/></svg>
        www.whitcombecpa.ca
      </li>
    </ul>
  </section>

  <section class="card card--back" aria-label="Business card, dark side">
    <div class="lockup mark">
      <span class="mark__square"></span>
      <div class="brand">
        <span class="brand__name">Dario Whitcombe, CPA LLC</span>
        <span class="brand__tagline">Certified Public Accountant</span>
      </div>
    </div>
    <p class="services">Accounting, Tax &amp; Consulting Services</p>
  </section>
</main>
</body>
</html>
```